VOMRA Pty Ltd Business Card

Looking for a simple yet eye-catching double-sided business card design using my company logo on one side and contact details on the other.

Target Market(s)

Government

Industry/Entity Type

Communication Systems Engineering

Contact Information for Business Card

VOMRA Pty Ltd

Requirements
Nice to have
• Would be great to have a QR code so details can be scanned into contacts

```html
<!DOCTYPE html>
<html lang="en">
<head>
<meta charset="utf-8">
<title>VOMRA Pty Ltd – Business Card</title>
<link rel="stylesheet" href="https://fonts.googleapis.com/css2?family=Open+Sans:wght@400;600;800&display=swap">
<style>
  :root {
    --backdrop: #222222;
    --card: #37414a;
    --card-deep: #2b343c;
    --gold: #e0a526;
    --gold-light: #f2c534;
    --silver: #b9bcc0;
    --ink: #1e262d;
  }
  * { box-sizing: border-box; margin: 0; padding: 0; }
  html, body {
    width: 1200px; height: 780px; overflow: hidden;
    background: var(--backdrop);
    font-family: "Open Sans", Arial, sans-serif;
  }
  .canvas {
    position: relative; width: 1200px; height: 780px;
    display: flex; justify-content: center; align-items: center; gap: 60px;
  }
  .card {
    position: relative; width: 400px; height: 655px;
    background: var(--card);
    border-bottom: 4px solid var(--gold);
    box-shadow: 0 18px 40px rgba(0,0,0,.45);
    overflow: hidden;
  }

  /* front side */
  .brand-artwork {
    position: absolute; left: 40px; top: 70px; width: 320px; height: 420px;
    background: radial-gradient(ellipse at 40% 45%, rgba(185,188,192,.28) 0%, rgba(43,52,60,.55) 55%, rgba(55,65,74,0) 80%);
  }
  .front-wordmark {
    position: absolute; right: 38px; bottom: 44px;
    font-weight: 800; font-size: 46px; letter-spacing: 4px;
    color: var(--gold);
  }

  /* back side */
  .back-header {
    position: absolute; left: 38px; top: 44px;
    display: flex; align-items: center; gap: 16px;
  }
  .brand-dot {
    width: 52px; height: 52px; border-radius: 50%;
    border: 3px solid var(--gold);
  }
  .back-wordmark {
    font-weight: 800; font-size: 44px; letter-spacing: 4px; color: var(--gold);
  }
  .details {
    position: absolute; left: 38px; right: 30px; top: 330px;
    color: var(--gold);
  }
  .person-name { font-weight: 800; font-size: 36px; line-height: 1.05; }
  .person-role { font-weight: 600; font-size: 17px; margin: 2px 0 10px 118px; }
  .dot-rule { display: block; width: 100%; height: 26px; }
  .contact-list { list-style: none; font-size: 17px; line-height: 1.45; margin: 6px 0 8px 118px; }
  .address { font-size: 17px; line-height: 1.4; margin: 8px 0 0 40px; }
</style>
</head>
<body>
<main class="canvas">

  <section class="card card-front" aria-label="Card front">
    <div class="brand-artwork" role="img" aria-label="Large embossed brand symbol artwork in silver and dark grey"></div>
    <div class="front-wordmark">VOMRA</div>
  </section>

  <section class="card card-back" aria-label="Card back">
    <header class="back-header">
      <span class="brand-dot"></span>
      <span class="back-wordmark">VOMRA</span>
    </header>

    <div class="details">
      <h1 class="person-name">Jordan Hale</h1>
      <p class="person-role">Co-Founder</p>

      <svg class="dot-rule" viewBox="0 0 330 26" aria-hidden="true">
        <g fill="var(--gold)">
          <circle cx="6" cy="13" r="2.5"/><circle cx="20" cy="13" r="3.5"/><circle cx="36" cy="13" r="4.5"/>
          <circle cx="54" cy="13" r="5.5"/><circle cx="74" cy="13" r="6.5"/><circle cx="96" cy="13" r="7.5"/>
        </g>
        <g>
          <circle cx="130" cy="13" r="12" fill="var(--gold)"/>
          <path d="M124 8 q2-2 4 0 l1 3 -2 1 q1 3 4 4 l1-2 3 1 q2 2 0 4 q-5 1 -9-3 q-4-4 -2-8z" fill="var(--ink)"/>
          <circle cx="160" cy="13" r="12" fill="var(--gold)"/>
          <rect x="153" y="8" width="14" height="10" rx="1" fill="none" stroke="var(--ink)" stroke-width="1.6"/>
          <path d="M153 9 l7 5 7-5" fill="none" stroke="var(--ink)" stroke-width="1.6"/>
          <circle cx="190" cy="13" r="12" fill="var(--gold)"/>
          <circle cx="190" cy="13" r="7" fill="none" stroke="var(--ink)" stroke-width="1.6"/>
          <path d="M183 13 h14 M190 6 q-4 7 0 14 M190 6 q4 7 0 14" fill="none" stroke="var(--ink)" stroke-width="1.3"/>
        </g>
        <g fill="var(--gold)">
          <circle cx="220" cy="13" r="7.5"/><circle cx="242" cy="13" r="6.5"/><circle cx="262" cy="13" r="5.5"/>
          <circle cx="280" cy="13" r="4.5"/><circle cx="296" cy="13" r="3.5"/><circle cx="310" cy="13" r="2.5"/>
          <circle cx="322" cy="13" r="2"/>
        </g>
      </svg>

      <ul class="contact-list">
        <li>(555) 014-2290</li>
        <li>www.vomra.com.au</li>
        <li>admin@vomra.com.au</li>
      </ul>

      <svg class="dot-rule" viewBox="0 0 330 26" aria-hidden="true">
        <g fill="var(--gold)">
          <circle cx="6" cy="13" r="2.5"/><circle cx="20" cy="13" r="3.5"/><circle cx="36" cy="13" r="4.5"/>
          <circle cx="54" cy="13" r="5.5"/><circle cx="74" cy="13" r="6.5"/><circle cx="96" cy="13" r="7.5"/>
          <circle cx="120" cy="13" r="8"/>
        </g>
        <g>
          <circle cx="152" cy="13" r="12" fill="var(--gold)"/>
          <path d="M152 21 q-6-7 -6-11 a6 6 0 0 1 12 0 q0 4 -6 11z" fill="var(--ink)"/>
          <circle cx="152" cy="10" r="2.2" fill="var(--gold)"/>
        </g>
        <g fill="var(--gold)">
          <circle cx="184" cy="13" r="8"/><circle cx="208" cy="13" r="7.5"/><circle cx="230" cy="13" r="6.5"/>
          <circle cx="250" cy="13" r="5.5"/><circle cx="268" cy="13" r="4.5"/><circle cx="284" cy="13" r="3.5"/>
          <circle cx="298" cy="13" r="2.5"/><circle cx="312" cy="13" r="2"/>
        </g>
      </svg>

      <p class="address">14-16 Harlow Street Eastvale<br>NSW 2099 Australia</p>
    </div>
  </section>

</main>
</body>
</html>
```